Business Card Design Project

I need a business card designed from scratch. I have an existing logo that I can upload in Illustrator for modification or redesign.

The Company is called Query Lanterns http://querylanterns.com.au and we provide Search Engine Optimization services to Australian businesses. The current logo signifies an increase in visitors, profits etc...

There are no restrictions as to the redesign - colours, style etc are all open to change.

Cards will be full colour and one sided printed at http://www.cardmoxel.com.au so check their requirements for file format and sizes etc.

I will expect all original files upon completion of project.

Target Market(s)

Any business with a web site looking to improve their search engine rankings

Industry/Entity Type

Business

Requirements
Must have
• I like modern, sleek designs. Clean, not fussy, uncluttered.

```html
<!DOCTYPE html>
<html lang="en">
<head>
<meta charset="utf-8">
<title>Query Lanterns — Business Card</title>
<link rel="stylesheet" href="https://fonts.googleapis.com/css2?family=Open+Sans:wght@700;800&family=PT+Sans+Narrow:wght@700&display=swap">
<style>
  :root {
    --page: #e9e9e7;
    --card: #ffffff;
    --band: #f6c41a;
    --band-edge: #1d5f9e;
    --brand-blue: #1f6fb5;
    --deep-blue: #1b4f92;
    --ink-yellow: #f7c21c;
  }
  * { box-sizing: border-box; margin: 0; padding: 0; }
  html, body {
    width: 1189px; height: 1200px; overflow: hidden;
    background: var(--page);
  }
  .canvas { position: relative; width: 1189px; height: 1200px; }

  .card {
    position: absolute; left: 223px; width: 732px; height: 451px;
    background: var(--card);
    box-shadow: 0 6px 18px rgba(0,0,0,0.18);
    overflow: hidden;
  }
  .card--front { top: 73px; }
  .card--back { top: 663px; }

  .band {
    position: absolute; left: 0; right: 0; height: 31px;
    background: var(--band);
  }
  .band--top { top: 0; border-bottom: 2px solid var(--band-edge); }
  .band--bottom { bottom: 0; border-top: 2px solid var(--band-edge); }

  .wordmark {
    position: absolute; display: flex; align-items: center; gap: 14px;
    font-family: "Open Sans", sans-serif; font-weight: 800;
    color: var(--brand-blue); white-space: nowrap; letter-spacing: -0.5px;
  }
  .wordmark__dot {
    border-radius: 50%; background: var(--ink-yellow); flex: none;
  }
  .card--front .wordmark { left: 50%; top: 50%; transform: translate(-50%, -50%); font-size: 50px; }
  .card--front .wordmark__dot { width: 40px; height: 40px; }
  .card--back .wordmark { left: 14px; top: 44px; font-size: 26px; gap: 8px; }
  .card--back .wordmark__dot { width: 18px; height: 18px; }

  .contact-ribbon {
    position: absolute; left: 31px; top: 84px; width: 413px; height: 313px;
    border-radius: 28px;
    background: linear-gradient(160deg, #f8cf3a 0%, #f3b81a 45%, #2a68ad 100%);
  }
  .contact {
    position: absolute; font-family: "Open Sans", sans-serif; font-weight: 700;
    white-space: nowrap; transform-origin: left center;
  }
  .contact--phone { left: 70px; top: 235px; font-size: 19px; color: var(--deep-blue); transform: rotate(-20deg); }
  .contact--web { left: 62px; top: 278px; font-size: 15px; color: #ffffff; transform: rotate(-6deg); }
  .contact--mail { left: 168px; top: 378px; font-size: 14px; color: var(--deep-blue); transform: rotate(-40deg); }

  .holder {
    position: absolute; left: 491px; top: 312px;
    font-family: "PT Sans Narrow", sans-serif; font-weight: 700; color: var(--brand-blue);
  }
  .holder__name { font-size: 23px; line-height: 1.1; }
  .holder__role { font-size: 18px; line-height: 1.2; }
</style>
</head>
<body>
<div class="canvas">
  <section class="card card--front">
    <div class="band band--top"></div>
    <div class="wordmark"><span class="wordmark__dot"></span>Query Lanterns</div>
    <div class="band band--bottom"></div>
  </section>

  <section class="card card--back">
    <div class="band band--top"></div>
    <div class="wordmark"><span class="wordmark__dot"></span>Query Lanterns</div>
    <div class="contact-ribbon" role="img" aria-label="Brand ribbon graphic rising in a zigzag toward an arrow, carrying the contact details"></div>
    <p class="contact contact--phone">1300 482915</p>
    <p class="contact contact--web">www.querylanterns.com.au</p>
    <p class="contact contact--mail">miles@querylanterns.com.au</p>
    <div class="holder">
      <p class="holder__name">Miles Harlow</p>
      <p class="holder__role">Internet Marketing Consultant</p>
    </div>
    <div class="band band--bottom"></div>
  </section>
</div>
</body>
</html>
```